Bookcover: Ways to Turn Into a Bold Pathfinder

I am publishing a super-low-cost innovation book for €4,99 on Quillmere Open Press to help everyone become a great innovator: young ambitious people without college education nor a big budget. Do you want to help me?

Brief:
Design a book cover 1600 x 2560 pixels for QOP.
Main title: Ways to Turn Into a Bold Pathfinder
Sub title: mindset - insights - skills & tools
Author: Joost ter Brakel
Design: captive, and appealing to everyone
Target Group: young ambitious people without college education

For quillmere please format the height/width ratio of 1.6:1

```html
<!DOCTYPE html>
<html lang="en">
<head>
<meta charset="utf-8">
<title>Ways to Turn Into a Bold Pathfinder — Book Cover</title>
<link rel="stylesheet" href="https://fonts.googleapis.com/css2?family=Poppins:wght@700&family=Montserrat:wght@600;700&display=swap">
<style>
  :root {
    --backdrop: #8c8c8c;
    --cover-yellow: #e6b23a;
    --cover-yellow-deep: #e2a82c;
    --cover-yellow-light: #e9bf5a;
    --glow: #f6e6bd;
    --ink: #2a2624;
    --accent-wine: #7e2e45;
    --band: #2b2a29;
    --band-text: #f2f2f2;
  }
  * { margin: 0; padding: 0; box-sizing: border-box; }
  html, body {
    width: 1200px;
    height: 1200px;
    overflow: hidden;
    background: var(--backdrop);
  }
  .book-cover {
    position: absolute;
    left: 275px;
    top: 80px;
    width: 650px;
    height: 1040px;
    overflow: hidden;
    background: linear-gradient(180deg, var(--cover-yellow-light) 0%, var(--cover-yellow) 45%, var(--cover-yellow-deep) 100%);
  }
  .background-pattern {
    position: absolute;
    inset: 0;
    background: radial-gradient(ellipse at 50% 55%, rgba(240, 200, 100, 0.35) 0%, rgba(230, 178, 58, 0) 70%);
  }
  .lamp-illustration {
    position: absolute;
    left: 0;
    top: 0;
    width: 650px;
    height: 420px;
    background: radial-gradient(ellipse 60% 70% at 50% 35%, var(--glow) 0%, rgba(246, 230, 189, 0.5) 40%, rgba(230, 178, 58, 0) 75%);
  }
  .title {
    position: absolute;
    left: 0;
    top: 385px;
    width: 650px;
    text-align: center;
    font-family: "Poppins", sans-serif;
    font-weight: 700;
    color: var(--ink);
  }
  .title-line {
    display: block;
    font-size: 50px;
    line-height: 78px;
    letter-spacing: 4px;
  }
  .title-highlight {
    display: block;
    margin-top: -4px;
    font-size: 70px;
    line-height: 88px;
    letter-spacing: 6px;
    color: var(--accent-wine);
  }
  .pillars {
    position: absolute;
    left: 0;
    top: 822px;
    width: 650px;
    height: 120px;
  }
  .pillar {
    position: absolute;
    top: 0;
    width: 190px;
    margin-left: -95px;
    text-align: center;
  }
  .pillar-icon {
    display: block;
    margin: 0 auto;
    width: 72px;
    height: 72px;
  }
  .pillar-label {
    display: block;
    margin-top: 22px;
    font-family: "Montserrat", sans-serif;
    font-weight: 700;
    font-size: 21px;
    letter-spacing: 2.5px;
    color: var(--ink);
  }
  .pillar-mindset { left: 145px; }
  .pillar-insights { left: 338px; }
  .pillar-tools { left: 525px; }
  .author-band {
    position: absolute;
    left: 0;
    bottom: 0;
    width: 650px;
    height: 50px;
    background: var(--band);
    display: flex;
    align-items: center;
    justify-content: center;
  }
  .author-name {
    font-family: "Montserrat", sans-serif;
    font-weight: 600;
    font-size: 20px;
    letter-spacing: 2.5px;
    color: var(--band-text);
    text-transform: uppercase;
  }
</style>
</head>
<body>
  <main class="book-cover">
    <div class="background-pattern" role="img" aria-label="Faint hand-drawn sun and swirl doodle pattern"></div>
    <div class="lamp-illustration" role="img" aria-label="Illustration of a hanging pendant lamp casting a cone of light"></div>

    <h1 class="title">
      <span class="title-line">Ways</span>
      <span class="title-line">to</span>
      <span class="title-line">Turn Into</span>
      <span class="title-line">a Bold</span>
      <span class="title-highlight">Pathfinder</span>
    </h1>

    <section class="pillars">
      <div class="pillar pillar-mindset">
        <svg class="pillar-icon" viewBox="0 0 72 72" role="img" aria-label="Icon of a head with a light bulb">
          <circle cx="36" cy="36" r="26" fill="var(--ink)"/>
        </svg>
        <span class="pillar-label">MINDSET</span>
      </div>
      <div class="pillar pillar-insights">
        <svg class="pillar-icon" viewBox="0 0 72 72" role="img" aria-label="Icon of a light bulb with an eye">
          <circle cx="36" cy="36" r="26" fill="none" stroke="var(--ink)" stroke-width="3"/>
        </svg>
        <span class="pillar-label">INSIGHTS</span>
      </div>
      <div class="pillar pillar-tools">
        <svg class="pillar-icon" viewBox="0 0 72 72" role="img" aria-label="Icon of two gears">
          <circle cx="36" cy="36" r="26" fill="var(--ink)"/>
        </svg>
        <span class="pillar-label">TOOLS</span>
      </div>
    </section>

    <footer class="author-band">
      <span class="author-name">Joost ter Brakel</span>
    </footer>
  </main>
</body>
</html>
```